CANNABIS BASED BUSINESS CARD DESIGN AND CREATION

WE ARE A PRIVATELY OWNED INVESTMENT CORPORATION. WE PRIMARILY INVEST IN LEGAL PUBLICALLY TRADED CANNABIS COMPANIES THAT ARE TRADED THROUGH THE OTC OR VOLTRIX. WE OFFER THE PUBLIC AN OPPORTUNITY TO PARTICIPATE DIRECTLY WITH THESE COMPANIES FOR NO FEES, NO COMMISSIONS AND IN DEPTH RESEARCH ON EVERY COMPANY PROFILE. WE ARE ALSO PRO FEDERAL LEGALIZATION AND WILL APPLY FOR CULTIVATION AND DISPENSARY LICENSES WHEN THEY BECOME AVAILABLE.

Target Market(s)

30-60 FEMALE AND MALE INVESTORS

Industry/Entity Type

Business

Contact Information for Business Card

EDS CAPITAL GROUP CORPERIN D SLAUGHTER(469) 426-6302ERIN@EDSCAPITALGROUP.COM

Font styles to use
Decorative

Requirements
Must have
• COMPANY LOGO
• CANNABIS LOGO
Nice to have
• MODERN FONT AND LOGOS

```html
<!DOCTYPE html>
<html lang="en">
<head>
<meta charset="utf-8">
<title>Verdance Holdings – Business Card</title>
<link href="https://fonts.googleapis.com/css2?family=Lato:wght@400;700&display=swap" rel="stylesheet">
<style>
  :root {
    --backdrop: #6f7d16;
    --card-black: #050505;
    --card-sheen: #1c1c1c;
    --brand-green: #1fb54a;
    --leaf-tint: #262626;
    --text-light: #f2f2f2;
    --text-muted: #a9a9a9;
    --rule: #2c2c2c;
  }
  * { box-sizing: border-box; margin: 0; padding: 0; }
  html, body { width: 1200px; height: 900px; overflow: hidden; }
  body {
    background: var(--backdrop);
    font-family: "Lato", Arial, sans-serif;
    position: relative;
  }
  .card {
    position: absolute;
    width: 600px;
    height: 340px;
    background: radial-gradient(ellipse at 70% 30%, var(--card-sheen) 0%, var(--card-black) 65%);
    box-shadow: 0 14px 30px rgba(0,0,0,0.45);
    overflow: hidden;
  }
  .card--front { left: 90px; top: 90px; }
  .card--back { left: 510px; top: 470px; }

  .leaf-decoration {
    position: absolute;
    right: 30px;
    top: 20px;
    width: 260px;
    height: 260px;
    border-radius: 50%;
    background: radial-gradient(circle, var(--leaf-tint) 0%, rgba(38,38,38,0) 70%);
  }
  .brand {
    position: absolute;
    display: flex;
    align-items: center;
    gap: 10px;
    color: var(--brand-green);
    font-weight: 700;
    letter-spacing: 0.06em;
    white-space: nowrap;
  }
  .brand__dot {
    border-radius: 50%;
    background: var(--brand-green);
    flex: none;
  }
  .card--front .brand { left: 0; right: 0; top: 150px; justify-content: center; font-size: 28px; }
  .card--front .brand__dot { width: 22px; height: 22px; }

  .card--back .brand { right: 34px; top: 70px; font-size: 18px; }
  .card--back .brand__dot { width: 14px; height: 14px; }

  .card__rule {
    position: absolute;
    left: 30px;
    right: 30px;
    top: 170px;
    height: 1px;
    background: var(--rule);
  }
  .holder-name {
    position: absolute;
    left: 34px;
    top: 250px;
    color: var(--text-light);
    font-size: 16px;
    letter-spacing: 0.03em;
  }
  .contact-list {
    position: absolute;
    right: 30px;
    top: 190px;
    list-style: none;
    color: var(--text-muted);
    font-size: 12px;
  }
  .contact-list li { display: flex; align-items: center; gap: 10px; margin-bottom: 7px; }
  .contact-list svg { width: 12px; height: 12px; fill: var(--brand-green); flex: none; }
</style>
</head>
<body>
  <section class="card card--front" aria-label="Business card front">
    <div class="leaf-decoration" role="img" aria-label="Faint cannabis leaf decoration"></div>
    <div class="brand"><span class="brand__dot"></span>VERDANCE HOLDINGS</div>
  </section>

  <section class="card card--back" aria-label="Business card back">
    <div class="brand"><span class="brand__dot"></span>VERDANCE HOLDINGS</div>
    <div class="card__rule"></div>
    <p class="holder-name">MARLA J PENDLEBURY</p>
    <ul class="contact-list">
      <li>
        <svg viewBox="0 0 24 24" aria-hidden="true"><path d="M6.6 10.8a15.1 15.1 0 0 0 6.6 6.6l2.2-2.2c.3-.3.7-.4 1-.2 1.1.4 2.3.6 3.6.6.6 0 1 .4 1 1V20c0 .6-.4 1-1 1A17 17 0 0 1 3 4c0-.6.4-1 1-1h3.5c.6 0 1 .4 1 1 0 1.3.2 2.5.6 3.6.1.3 0 .7-.2 1z"/></svg>
        (555) 013-4478
      </li>
      <li>
        <svg viewBox="0 0 24 24" aria-hidden="true"><path d="M2 5h20v14H2z M2 5l10 8 10-8" /></svg>
        marla@verdanceholdings-demo.com
      </li>
      <li>
        <svg viewBox="0 0 24 24" aria-hidden="true"><path d="M10 14a4 4 0 0 1 0-5.7l3-3a4 4 0 0 1 5.7 5.7l-1.5 1.5-1.4-1.4 1.5-1.5a2 2 0 0 0-2.9-2.9l-3 3a2 2 0 0 0 0 2.9zm4-4a4 4 0 0 1 0 5.7l-3 3a4 4 0 0 1-5.7-5.7l1.5-1.5 1.4 1.4-1.5 1.5a2 2 0 0 0 2.9 2.9l3-3a2 2 0 0 0 0-2.9z"/></svg>
        www.verdanceholdings-demo.com
      </li>
    </ul>
  </section>
</body>
</html>
```